New signage for apartment community in the Pacific Northwest

Signage for an apartment community in the Pacific Northwest. It should have a contemporary northwest vibe with a fresh exciting feeling. We are open to the colors cayenne, white, charcoal and a splash of lime green. Sign to have the name 'VOLTE' with the address number 28351 smaller underneath. sign can include a shape under the name or a feeling of energy in the shape of the name.

Target Market(s)

Young urban professionals

Industry/Entity Type

Real Estate Development

Requirements
Must have
• eyecatching
Should not have
• anything too cute or too busy

```html
<!DOCTYPE html>
<html lang="en">
<head>
<meta charset="utf-8">
<title>VOLTE — Community Sign</title>
<link rel="stylesheet" href="https://fonts.googleapis.com/css2?family=Playfair+Display:wght@700;800&family=Montserrat:wght@600&display=swap">
<style>
  :root {
    --backdrop: #5a5a5a;
    --lime: #84c100;
    --lime-deep: #76ae00;
    --lime-shadow: #5f8f00;
    --cayenne: #b00000;
    --white: #ffffff;
  }
  * { margin: 0; padding: 0; box-sizing: border-box; }
  html, body {
    width: 796px;
    height: 1200px;
    overflow: hidden;
  }
  body {
    background: var(--backdrop);
    position: relative;
  }
  .sign {
    position: absolute;
    left: 58px;
    top: 373px;
    width: 680px;
    height: 453px;
    box-shadow: 0 6px 18px rgba(0, 0, 0, 0.35);
    overflow: hidden;
  }
  .sign__field {
    position: absolute;
    left: 0; top: 0;
    width: 680px;
    height: 300px;
  }
  .sign__field svg { display: block; }
  .sign__band {
    position: absolute;
    left: 0; top: 300px;
    width: 680px;
    height: 153px;
    background: var(--cayenne);
  }
  .sign__frame {
    position: absolute;
    left: 19px; top: 19px;
    right: 19px; bottom: 19px;
    border: 1px solid var(--white);
    pointer-events: none;
  }
  .sign__name {
    position: absolute;
    left: 0; right: 0;
    top: 52px;
    text-align: center;
    font-family: "Playfair Display", Georgia, serif;
    font-weight: 800;
    font-size: 168px;
    line-height: 1;
    color: var(--white);
    text-shadow: -3px 4px 0 var(--lime-shadow);
    letter-spacing: 0.01em;
  }
  .sign__address {
    position: absolute;
    left: 0; right: 0;
    top: 364px;
    display: flex;
    align-items: center;
    justify-content: center;
    gap: 26px;
    font-family: "Montserrat", Arial, sans-serif;
    font-weight: 600;
    font-size: 17px;
    letter-spacing: 0.32em;
    color: var(--white);
  }
  .sign__rule {
    width: 60px;
    height: 1px;
    background: var(--white);
  }
</style>
</head>
<body>
  <main class="sign">
    <div class="sign__field">
      <svg width="680" height="300" role="img" aria-label="Lime green sunburst rays radiating from the centre">
        <defs>
          <radialGradient id="burst" cx="50%" cy="100%" r="110%">
            <stop offset="0%" stop-color="#7cb500"/>
            <stop offset="100%" stop-color="#86c300"/>
          </radialGradient>
        </defs>
        <rect width="680" height="300" fill="url(#burst)"/>
      </svg>
    </div>
    <div class="sign__band"></div>
    <div class="sign__frame"></div>
    <h1 class="sign__name">VOLTE</h1>
    <p class="sign__address">
      <span class="sign__rule"></span>
      <span class="sign__address-text">28351, PACIFIC NORTHWEST</span>
      <span class="sign__rule"></span>
    </p>
  </main>
</body>
</html>
```